Realty Group Needs Classy, Contemporary Letterhead Design

We need a letterhead design for a new realty company located in NY, USA. We buy investment properties to rehabilitate and or keep in our rental portfolio.

```html
<!DOCTYPE html>
<html lang="en">
<head>
<meta charset="utf-8">
<title>Quorvane Realty Group – Letterhead</title>
<link href="https://fonts.googleapis.com/css2?family=Open+Sans:wght@400;600;700;800&display=swap" rel="stylesheet">
<style>
  :root {
    --brand-purple: #4b2687;
    --rule-grey: #8a8a8a;
    --ink: #3a3a3a;
    --paper: #ffffff;
    --backdrop: #e6e6e8;
    --on-brand: #ffffff;
    --icon-dot: #c9c2a0;
  }
  * { box-sizing: border-box; margin: 0; padding: 0; }
  html, body {
    width: 1200px; height: 795px; overflow: hidden;
    background: var(--backdrop);
    font-family: "Open Sans", Arial, sans-serif;
  }
  .letterhead {
    position: absolute; left: 338px; top: 27px;
    width: 524px; height: 741px;
    background: var(--paper);
    box-shadow: 0 2px 10px rgba(0,0,0,.12);
    overflow: hidden;
    color: var(--ink);
  }
  .letterhead__frame { position: absolute; inset: 0; }
  .brand-name {
    position: absolute; left: 40px; top: 92px;
    color: var(--brand-purple); font-weight: 800;
    font-size: 19px; line-height: 1; letter-spacing: .5px;
    display: flex; align-items: center; gap: 6px;
  }
  .brand-name__mark { width: 10px; height: 10px; background: var(--brand-purple); }
  .brand-name__tag { display: block; font-size: 7px; letter-spacing: 1px; margin-top: 3px; }
  .contact-list {
    position: absolute; left: 345px; top: 10px;
    list-style: none; color: var(--on-brand);
    font-size: 7px; line-height: 1.45;
  }
  .contact-list li { display: flex; align-items: center; gap: 4px; }
  .contact-list svg { width: 7px; height: 7px; flex: none; }
  .footer-web {
    position: absolute; right: 14px; bottom: 62px;
    color: var(--on-brand); font-size: 7.5px;
  }
  .letter {
    position: absolute; left: 62px; top: 166px; width: 420px;
    font-size: 8.4px; line-height: 1.4;
  }
  .letter__date { margin-bottom: 12px; }
  .letter__recipient { font-weight: 600; font-size: 9.5px; line-height: 1.35; margin-bottom: 12px; }
  .letter__salutation { font-weight: 700; font-size: 9.5px; margin-bottom: 12px; }
  .letter__body p { margin-bottom: 12px; text-align: justify; }
  .letter__closing { margin-top: 18px; }
  .letter__signature {
    display: block; width: 64px; height: 16px; margin-top: 8px;
    background: linear-gradient(90deg, rgba(30,30,30,.15), rgba(30,30,30,.35));
    border-radius: 8px;
  }
</style>
</head>
<body>
<main class="letterhead">
  <svg class="letterhead__frame" viewBox="0 0 524 741" aria-hidden="true">
    <polygon points="340,0 524,0 524,78 298,78" fill="var(--brand-purple)"/>
    <polyline points="294,84 262,140 54,140 26,190 26,430" fill="none" stroke="var(--rule-grey)" stroke-width="2"/>
    <polygon points="412,640 524,590 524,692 376,692" fill="var(--brand-purple)"/>
  </svg>

  <div class="brand-name">
    <span class="brand-name__mark"></span>
    <span>QUORVANE<span class="brand-name__tag">REALTY GROUP LLC</span></span>
  </div>

  <ul class="contact-list">
    <li>Suite 410 Harbor Avenue, New York,</li>
    <li>NY 10001 USA</li>
    <li><svg viewBox="0 0 10 10"><circle cx="5" cy="5" r="5" fill="var(--icon-dot)"/></svg>(00) 5550 142 310</li>
    <li><svg viewBox="0 0 10 10"><circle cx="5" cy="5" r="5" fill="var(--icon-dot)"/></svg>(00) 5550 142 311</li>
    <li><svg viewBox="0 0 10 10"><circle cx="5" cy="5" r="5" fill="var(--icon-dot)"/></svg>hello@quorvanerealty.example</li>
  </ul>

  <section class="letter">
    <p class="letter__date">January 12, 2021</p>
    <p class="letter__recipient">Mr. John Doe<br>President<br>AA Corporation<br>111 Street Name, Suite#<br>City, State, 12345</p>
    <p class="letter__salutation">Dear Mr. John,</p>
    <div class="letter__body">
      <p>Lorem Ipsum is simply dummy text of the printing and typesetting industry. Lorem Ipsum has been the industry's standard dummy text ever since the 1500s, when an unknown printer took a galley of type and scrambled it to make a type specimen book. It has survived not only five centuries, but also the leap into electronic typesetting, remaining essentially unchanged.</p>
      <p>The standard chunk of Lorem Ipsum used since the 1500s is reproduced below for those interested. Sections 1.10.32 and 1.10.33 from "the early sample sheets" of the print trade are also reproduced in their exact original form, accompanied by English versions from the 1914 translation by the type foundry.</p>
      <p>Lorem Ipsum is simply dummy text of the printing and typesetting industry. Lorem Ipsum has been the industry's standard dummy text ever since the 1500s, when an unknown printer took a galley of type and scrambled it to make a type specimen book. It has survived not only five centuries, but also the leap into electronic typesetting, remaining essentially unchanged. It was popularised in the</p>
    </div>
    <p class="letter__closing">Sincerely Your,</p>
    <span class="letter__signature" role="img" aria-label="Handwritten signature of the sender"></span>
  </section>

  <p class="footer-web">www.quorvanerealty.example</p>
</main>
</body>
</html>
```